Business Card

THIS IS THE CARD INFORMATION
DEVELOPMENT I FINANCING I PROPERTY MANAGEMENT
DANIEL OKAFOR
3182 SW 74th Terrace
Palm Crest, FL 33490
Telephone I 855.437.2618
Facsimile I 855.437.2675
Industry/Entity Type
Business

```html
<!DOCTYPE html>
<html lang="en">
<head>
<meta charset="utf-8">
<title>Rivera Castell &amp; Company – Business Card</title>
<link rel="stylesheet" href="https://fonts.googleapis.com/css2?family=Source+Sans+3:wght@300;400;700;800&display=swap">
<style>
  :root {
    --stage: #2b2929;
    --plum-light: #9c2386;
    --plum-dark: #711f68;
    --plum-deep: #4b1246;
    --paper: #ffffff;
    --ink: #1b1b1b;
    --on-plum: #ffffff;
  }
  * { margin: 0; padding: 0; box-sizing: border-box; }
  html, body {
    width: 1200px; height: 1000px; overflow: hidden;
    background: var(--stage);
    font-family: "Source Sans 3", "Myriad Pro", Arial, sans-serif;
  }
  .card {
    position: absolute; left: 109px; top: 200px;
    width: 978px; height: 578px;
    background: var(--paper);
    overflow: hidden;
  }
  .card__band {
    position: absolute; left: 0; top: 0; width: 100%; height: 348px;
    background: linear-gradient(90deg, var(--plum-light) 0%, var(--plum-dark) 100%);
  }
  .card__services {
    position: absolute; left: 44px; top: 38px;
    color: var(--on-plum); font-weight: 300; font-size: 26px; letter-spacing: 1.2px;
    white-space: nowrap;
  }
  .card__services .divider { font-size: 32px; margin: 0 1px; vertical-align: -3px; letter-spacing: 0; }
  .card__name {
    position: absolute; left: 46px; top: 104px;
    color: var(--on-plum); font-weight: 300; font-size: 40px; letter-spacing: 1px;
    white-space: nowrap;
  }
  .card__address, .card__contact {
    position: absolute; left: 48px;
    color: var(--on-plum); font-weight: 400; font-size: 21px; line-height: 31px;
    letter-spacing: 0.3px; white-space: nowrap;
  }
  .card__address { top: 168px; }
  .card__contact { top: 252px; line-height: 28px; }
  .card__contact .label { display: inline-block; width: 112px; }
  .brand {
    position: absolute; left: 48px; top: 427px;
    display: flex; align-items: center; gap: 12px;
  }
  .brand__dot {
    width: 80px; height: 80px; border-radius: 50%;
    background: var(--plum-light);
  }
  .brand__name {
    color: var(--ink); font-weight: 800; font-size: 40px; line-height: 38px;
    letter-spacing: -0.5px; white-space: nowrap;
  }
  .brand__name small { display: block; font-size: 22px; line-height: 24px; letter-spacing: 0; }
  .card__emblem { position: absolute; left: 593px; top: 198px; }
</style>
</head>
<body>
  <div class="card">
    <div class="card__band"></div>
    <p class="card__services">DEVELOPMENT<span class="divider">/</span>FINANCING<span class="divider">/</span>PROPERTY MANAGEMENT</p>
    <h1 class="card__name">DANIEL OKAFOR</h1>
    <p class="card__address">3182 SW 74th Terrace<br>Palm Crest, FL 33490</p>
    <p class="card__contact">
      <span class="label">Telephone :</span>855.437.2618<br>
      <span class="label">Facsimile&nbsp;&nbsp;&nbsp;:</span>855.437.2675
    </p>
    <div class="brand">
      <span class="brand__dot"></span>
      <p class="brand__name">RIVERA CASTELL<small>&amp; COMPANY</small></p>
    </div>
    <svg class="card__emblem" width="320" height="320" viewBox="0 0 320 320" aria-hidden="true">
      <circle cx="160" cy="160" r="160" fill="var(--plum-deep)"/>
    </svg>
  </div>
</body>
</html>
```